Anzeigengestaltung für eine Stellenanzeige
Zielgruppe
Stellenanzeige
Wir sind eine Druckerei. Wir suchen für unsere Druckerei einen Buchhalter/in oder bzw. auch für das Rechnungswesen.
Aufgabenstellung
Wir möchten eine Stellenanzeige mit klarer und schneller Wirkung , keine Fließtextanzeige und einer unnötigen Beschreibung wie toll unserer Druckerei ausgestattet ist. Die Anzeige darf bunt und lustig sein Wortspiele wie Zahlenbändiger o.ä. sind erlaubt. Die Stelle soll für 30 bis 40 Stunden Wochenarbeitsstunden ausgeschrieben sein.
Mehr möchten wir gar nicht sagen wir sind ja nicht die kreativsten :-)
Unsere Hausfarbe sind HKS 38 und HKS 6

```html
<!DOCTYPE html>
<html lang="de">
<head>
<meta charset="utf-8">
<title>Stellenanzeige Buchhalter/in</title>
<link href="https://fonts.googleapis.com/css2?family=Inter:wght@300;400;700;800&display=swap" rel="stylesheet">
<style>
  :root {
    --orange: #d9821e;
    --navy: #1d2d4a;
    --ink: #0d0d0d;
    --paper: #ffffff;
    --track-light: #b9bfc8;
    --track-dark: #6f7b90;
    --grass: #c9cf52;
  }
  * { margin: 0; padding: 0; box-sizing: border-box; }
  html, body { width: 1200px; height: 848px; overflow: hidden; background: var(--paper); }
  body { font-family: "Inter", Helvetica, Arial, sans-serif; color: var(--ink); }

  .ad { position: relative; width: 1200px; height: 848px; background: var(--paper); }

  .hero {
    position: absolute; left: 0; top: 0; width: 1148px; height: 660px;
    border-right: 9px solid var(--orange);
    border-bottom: 9px solid var(--orange);
    border-bottom-right-radius: 28px;
    overflow: hidden;
  }
  .hero-photo {
    position: absolute; inset: 0;
    background:
      linear-gradient(160deg, transparent 0 58%, rgba(201,207,82,0) 58%),
      linear-gradient(195deg, var(--grass) 0 9%, transparent 9.5%),
      linear-gradient(170deg, var(--track-light) 0%, #9ea6b3 45%, var(--track-dark) 100%);
  }

  .headline {
    position: absolute; left: 60px; top: 82px;
    font-size: 78px; font-weight: 700; line-height: 83px; letter-spacing: -0.5px;
  }

  .offer {
    position: absolute; left: 0; top: 386px; width: 811px; height: 163px;
    background: rgba(235, 237, 242, 0.82);
    border: 2px solid var(--orange); border-left: none;
    border-radius: 0 20px 20px 0;
    padding: 32px 0 0 58px;
    font-size: 39px; font-weight: 300; line-height: 46px;
  }

  .footer { position: absolute; left: 0; top: 690px; width: 100%; height: 158px; }
  .contact { position: absolute; top: 14px; font-size: 19px; line-height: 27px; }
  .contact-address { left: 56px; }
  .contact-address .label { font-weight: 700; }
  .contact-lines { left: 306px; }

  .brand {
    position: absolute; right: 55px; top: 16px;
    display: flex; align-items: center; gap: 14px;
  }
  .brand-square { width: 62px; height: 62px; background: var(--orange); border-radius: 8px; }
  .brand-name { font-size: 36px; font-weight: 800; color: var(--navy); letter-spacing: -0.5px; }
</style>
</head>
<body>
<main class="ad">
  <section class="hero">
    <div class="hero-photo" role="img" aria-label="Foto: Sprinter startet aus dem Startblock auf einer blauen Laufbahn, Rasen oben rechts"></div>
    <h1 class="headline">Für alle die Zahlen<br>auch mal sportlich<br>nehmen.</h1>
    <p class="offer">Wir suchen eine/einen Buchhalter/in mit<br>Hang zum Rechnungswesen.</p>
  </section>

  <footer class="footer">
    <address class="contact contact-address" style="font-style:normal">
      <span class="label">Kontakt:</span><br>
      Kessler &amp; Brandt GmbH<br>
      Lindenweg 7<br>
      48999 Musterstadt
    </address>
    <p class="contact contact-lines">
      Telefon: +49 (0) 1234 5678-0<br>
      Telefax: +49 (0) 1234 5678-29<br>
      info@kessler-brandt.de
    </p>
    <div class="brand">
      <span class="brand-square"></span>
      <span class="brand-name">KESSLER &amp; BRANDT</span>
    </div>
  </footer>
</main>
</body>
</html>
```